Quorva - corporate Business Card

We need a good look and innovative business card for a new start up company based in Los Angeles called "Quorva". We are in a payment business, including payment card, app, and ewallet. We are expert in online payment and Card not present (CNP) transaction.
We need an innovative, modern business card.

Our logo font is Aero Matics

Target Market(s)

Startup - Bank - Online Payment - Card Manufacturing

Industry/Entity Type

Startup

Contact Information for Business Card

phone: 555 014 7396 - Address: 4172 Marlowe blvd, Tarrow Bay, OR 90299

Requirements
Must have
• Message: innovative, professional, expert, high tech, trust, online payment expert, security
Nice to have
• no comment
Should not have
• no Comment

```html
<!DOCTYPE html>
<html lang="en">
<head>
<meta charset="utf-8">
<title>Quorva business card</title>
<link href="https://fonts.googleapis.com/css2?family=Open+Sans:wght@400;600&family=Ubuntu:wght@500&display=swap" rel="stylesheet">
<style>
  :root {
    --brand-red: #d21f3c;
    --brand-red-deep: #b8172f;
    --card-white: #f7f7f6;
    --text-grey: #6b6b6b;
    --rule-grey: #c9c9c9;
    --watermark: #efefee;
    --backdrop: #e9e6e2;
  }
  html, body {
    margin: 0;
    width: 1200px;
    height: 780px;
    overflow: hidden;
    background: var(--backdrop);
  }
  .stage {
    position: relative;
    width: 1200px;
    height: 780px;
  }
  .card {
    position: absolute;
    top: 240px;
    width: 520px;
    height: 300px;
    border-radius: 3px;
    overflow: hidden;
    box-shadow: 0 6px 18px rgba(0,0,0,0.15);
    font-family: "Open Sans", Arial, sans-serif;
  }
  /* Front */
  .card-front {
    left: 50px;
    background: linear-gradient(135deg, #ffffff 0%, var(--card-white) 100%);
  }
  .front-strip {
    position: absolute;
    left: 0; top: 0; bottom: 0;
    width: 58px;
    background: linear-gradient(180deg, var(--brand-red) 0%, var(--brand-red-deep) 100%);
  }
  .front-rule {
    position: absolute;
    left: 64px; top: 0; bottom: 0;
    width: 1px;
    background: var(--rule-grey);
  }
  .front-watermark {
    position: absolute;
    right: -40px; top: -70px;
    width: 260px; height: 260px;
    border-radius: 50%;
    background: var(--watermark);
  }
  .front-mark {
    position: absolute;
    left: 18px; top: 34px;
    width: 66px; height: 66px;
    border-radius: 50%;
    background: #fff;
    border: 6px solid var(--brand-red);
    box-sizing: border-box;
  }
  .front-name {
    position: absolute;
    left: 96px; top: 26px;
    margin: 0;
    font-family: "Ubuntu", Arial, sans-serif;
    font-weight: 500;
    font-size: 62px;
    line-height: 1;
    color: var(--brand-red);
    letter-spacing: 0.5px;
  }
  .person {
    position: absolute;
    left: 150px; top: 126px;
  }
  .person-name {
    margin: 0;
    font-weight: 600;
    font-size: 18px;
    line-height: 1.1;
    color: var(--brand-red);
  }
  .person-role {
    margin: 0;
    font-size: 13px;
    color: var(--text-grey);
  }
  .contact-list {
    position: absolute;
    left: 150px; top: 186px;
    margin: 0; padding: 0;
    list-style: none;
    font-size: 13px;
    color: var(--text-grey);
  }
  .contact-list li {
    display: flex;
    align-items: center;
    gap: 6px;
    height: 20px;
  }
  .contact-icon {
    width: 14px; height: 14px;
    background: var(--brand-red);
    display: inline-flex;
    align-items: center;
    justify-content: center;
  }
  .address {
    position: absolute;
    right: 26px; bottom: 22px;
    margin: 0;
    text-align: right;
    font-style: normal;
    font-size: 13px;
    line-height: 1.4;
    color: var(--text-grey);
  }
  /* Back */
  .card-back {
    left: 630px;
    background: linear-gradient(135deg, #d9253f 0%, var(--brand-red-deep) 100%);
  }
  .back-lockup {
    position: absolute;
    left: 110px; top: 92px;
    display: flex;
    align-items: center;
    gap: 12px;
  }
  .back-mark {
    width: 74px; height: 74px;
    border-radius: 50%;
    background: #fff;
  }
  .back-name {
    margin: 0;
    font-family: "Ubuntu", Arial, sans-serif;
    font-weight: 500;
    font-size: 64px;
    line-height: 1;
    color: #fff;
  }
  .back-web {
    position: absolute;
    left: 110px; top: 188px;
    margin: 0;
    font-size: 14px;
    color: #f4d6db;
    letter-spacing: 0.3px;
  }
</style>
</head>
<body>
<main class="stage">
  <section class="card card-front" aria-label="Card front">
    <div class="front-watermark"></div>
    <div class="front-strip"></div>
    <div class="front-rule"></div>
    <div class="front-mark"></div>
    <h1 class="front-name">quorva</h1>
    <div class="person">
      <p class="person-name">Dana Whitfield</p>
      <p class="person-role">Managing Director</p>
    </div>
    <ul class="contact-list">
      <li>
        <span class="contact-icon">
          <svg width="10" height="10" viewBox="0 0 10 10"><path d="M2 1 L4 1 L4.6 3 L3.5 4 Q4.5 6 6 6.5 L7 5.4 L9 6 L9 8 Q9 9 8 9 Q1 8.5 1 2 Q1 1 2 1 Z" fill="#fff"/></svg>
        </span>
        555 014 7396
      </li>
      <li>
        <span class="contact-icon">
          <svg width="10" height="8" viewBox="0 0 10 8"><rect x="0.5" y="0.5" width="9" height="7" fill="none" stroke="#fff"/><path d="M0.5 0.5 L5 4.5 L9.5 0.5" fill="none" stroke="#fff"/></svg>
        </span>
        hello@quorvapay.com
      </li>
    </ul>
    <address class="address">4172 Marlowe blvd,<br>Tarrow Bay, OR 90299</address>
  </section>

  <section class="card card-back" aria-label="Card back">
    <div class="back-lockup">
      <div class="back-mark"></div>
      <h2 class="back-name">quorva</h2>
    </div>
    <p class="back-web">www.quorvapay.com</p>
  </section>
</main>
</body>
</html>
```